Hvac and insulation company needs good looking business card design

We are hvac and insulation company and looking for a new business cards that look to today standards designs

Target Market(s)

homeowners

Industry/Entity Type

Hvac

Contact Information for Business Card

Name: Walter Brinoku
Home comfort consultant
address: 4827 Dunmore St #215 Oakland, CA 94619
office: 888-316-2790
cell: 510-742-3185
Lic.# 584261
Email: walter@corvane-hvac.com
Web: corvane-hvac.com

Requirements
Must have
• clean and sleek look
Nice to have
• simple with a clean look
Should not have
• to busy business card

```html
<!DOCTYPE html>
<html lang="en">
<head>
<meta charset="utf-8">
<title>Corvane Home Solutions – Business Card</title>
<link rel="stylesheet" href="https://fonts.googleapis.com/css2?family=Roboto:wght@300;400;500&family=Roboto+Condensed:wght@400;700&display=swap">
<style>
  :root {
    --orange: #f48a20;
    --white: #ffffff;
    --paper: #f4f4f4;
    --ink: #4a4a4a;
    --muted: #8a8a8a;
    --rule: #9a9a9a;
    --band-grey: #a8a8a8;
    --stage: #2e2e2e;
  }
  * { box-sizing: border-box; margin: 0; padding: 0; }
  html, body { width: 1200px; height: 886px; overflow: hidden; }
  body {
    background: var(--stage);
    font-family: "Roboto", Arial, sans-serif;
    position: relative;
  }
  .card {
    position: absolute;
    width: 525px;
    height: 300px;
    border-radius: 16px;
    overflow: hidden;
    top: 293px;
  }

  /* Back side */
  .card-back { left: 50px; background: var(--orange); }
  .card-back .brand-mark {
    position: absolute;
    left: 0; right: 0; top: 112px;
    text-align: center;
    color: var(--white);
    font-size: 48px;
    font-weight: 500;
    letter-spacing: 1px;
  }
  .card-back .back-web {
    position: absolute;
    left: 0; right: 0; bottom: 40px;
    text-align: center;
    color: var(--white);
    font-size: 12px;
    font-weight: 400;
    letter-spacing: 7px;
  }

  /* Front side */
  .card-front { left: 625px; background: var(--paper); }
  .front-brand {
    position: absolute;
    right: 40px; top: 40px;
    display: flex; align-items: center; gap: 12px;
  }
  .front-brand .brand-square {
    width: 34px; height: 34px; background: var(--orange); border-radius: 3px;
  }
  .front-brand .brand-name {
    color: var(--orange);
    font-size: 40px; font-weight: 500; line-height: 1;
  }
  .front-brand .brand-tagline {
    color: var(--muted);
    font-size: 12px; font-weight: 300; letter-spacing: 3px;
    margin-top: 2px; text-align: right;
  }
  .front-rule {
    position: absolute;
    left: 36px; right: 32px; top: 128px;
    height: 1px; background: var(--rule);
  }
  .front-address {
    position: absolute;
    right: 34px; top: 142px;
    text-align: right;
    font-family: "Roboto Condensed", Arial, sans-serif;
    font-size: 14px; line-height: 18px;
    color: var(--ink);
  }
  .front-address .web-accent { color: var(--orange); }
  .person {
    position: absolute;
    left: 34px; top: 168px;
    font-family: "Roboto Condensed", Arial, sans-serif;
  }
  .person .name {
    color: var(--orange);
    font-size: 19px; font-weight: 700;
    text-transform: uppercase;
  }
  .person .title {
    color: var(--ink);
    font-size: 14px;
    text-transform: uppercase;
    padding-bottom: 4px;
    border-bottom: 1px solid var(--rule);
    display: inline-block;
  }
  .contact-list { list-style: none; margin-top: 5px; }
  .contact-list li {
    display: flex; align-items: center; gap: 8px;
    color: var(--ink);
    font-size: 14px; line-height: 17px;
  }
  .contact-list svg { width: 11px; height: 11px; fill: var(--orange); flex: none; }
  .front-band {
    position: absolute;
    left: 0; right: 0; bottom: 0; height: 14px;
    display: flex;
  }
  .front-band .band-orange { width: 46%; background: var(--orange); }
  .front-band .band-grey { flex: 1; background: var(--band-grey); }
</style>
</head>
<body>

<section class="card card-back">
  <div class="brand-mark">corvane</div>
  <div class="back-web">www.corvane-hvac.com</div>
</section>

<section class="card card-front">
  <div class="front-brand">
    <div class="brand-square"></div>
    <div>
      <div class="brand-name">corvane</div>
      <div class="brand-tagline">home solutions</div>
    </div>
  </div>

  <div class="front-rule"></div>

  <address class="front-address" style="font-style:normal">
    4827 Dunmore St #215<br>
    Oakland, CA 94619<br>
    www.<span class="web-accent">corvane-hvac</span>.com
  </address>

  <div class="person">
    <div class="name">Walter Brinoku</div>
    <div class="title">Home Comfort Consultant</div>
    <ul class="contact-list">
      <li>
        <svg viewBox="0 0 24 24"><path d="M6.6 10.8a15.1 15.1 0 0 0 6.6 6.6l2.2-2.2a1 1 0 0 1 1-.25 11.4 11.4 0 0 0 3.6.57 1 1 0 0 1 1 1V20a1 1 0 0 1-1 1A17 17 0 0 1 3 4a1 1 0 0 1 1-1h3.5a1 1 0 0 1 1 1c0 1.25.2 2.45.57 3.57a1 1 0 0 1-.25 1z"/></svg>
        888-316-2790
      </li>
      <li>
        <svg viewBox="0 0 24 24"><path d="M7 1h10a2 2 0 0 1 2 2v18a2 2 0 0 1-2 2H7a2 2 0 0 1-2-2V3a2 2 0 0 1 2-2zm0 3v14h10V4z"/></svg>
        510-742-3185
      </li>
      <li>
        <svg viewBox="0 0 24 24"><path d="M5 2h10l4 4v16H5zm3 8h8v2H8zm0 4h8v2H8z"/></svg>
        Lic.# 584261
      </li>
      <li>
        <svg viewBox="0 0 24 24"><path d="M2 5h20v14H2zm2 2v.5l8 5 8-5V7l-8 5z"/></svg>
        walter@corvane-hvac.com
      </li>
    </ul>
  </div>

  <div class="front-band">
    <div class="band-orange"></div>
    <div class="band-grey"></div>
  </div>
</section>

</body>
</html>
```